Corvane Holdings , new business card design

investment firm with corporate clients . need double sided business card , vertical and horizontal options ,logo must be clear. prefer pantone colors only and sharp design. website also www.corvane.ae

Khalid Bin Tarrafi
Managing Director
Tel. +971 4 387 2940
Mobile +971 50 518 2403
khalid@corvane.ae
Q-Span Plaza, officw 18-B07, Warqa Gardens, Dubai

Contact Information for Business Card

Khalid Bin Tarrafi
Managing Director

Font styles to use
Serif

Colors

Designer to choose colors to be used in the design.

```html
<!DOCTYPE html>
<html lang="en">
<head>
<meta charset="utf-8">
<title>Corvane Holdings — Business Card</title>
<link rel="stylesheet" href="https://fonts.googleapis.com/css2?family=Josefin+Sans:wght@300&family=Open+Sans:wght@400;700&display=swap">
<style>
  :root {
    --bg: #2b2b2d;
    --card: #f4f4f5;
    --ink: #1f2230;
    --panel-light: #6f6e78;
    --panel-dark: #3e3d55;
    --tab: #4a4a66;
    --panel-text: #f2f2f5;
    --muted: #6a6a72;
  }
  * { box-sizing: border-box; margin: 0; padding: 0; }
  html, body { width: 1200px; height: 900px; overflow: hidden; }
  body {
    background: var(--bg);
    position: relative;
    font-family: "Open Sans", Arial, sans-serif;
  }
  .card {
    position: absolute;
    left: 280px;
    width: 640px;
    height: 366px;
    background: var(--card);
    border-radius: 18px;
    overflow: hidden;
    box-shadow: 0 10px 30px rgba(0,0,0,0.45);
  }
  .card--front { top: 60px; }
  .card--back { top: 474px; }

  .wordmark {
    position: absolute;
    display: flex;
    align-items: center;
    gap: 14px;
    color: var(--ink);
    font-family: "Josefin Sans", Arial, sans-serif;
    font-weight: 300;
  }
  .wordmark__square {
    width: 14px; height: 14px;
    background: var(--ink);
  }
  .wordmark__text { display: flex; flex-direction: column; line-height: 1; }
  .wordmark__name { font-size: 40px; letter-spacing: 14px; }
  .wordmark__sub { font-size: 13px; letter-spacing: 12.5px; margin-top: 10px; }

  .card--front .wordmark { left: 34px; top: 150px; }
  .card--front .wordmark__name { font-size: 30px; letter-spacing: 8px; }
  .card--front .wordmark__sub { font-size: 10px; letter-spacing: 8.2px; margin-top: 8px; }

  .contact-panel {
    position: absolute;
    left: 330px; top: 0;
    width: 310px; height: 100%;
    background: linear-gradient(160deg, var(--panel-light) 0%, var(--panel-dark) 100%);
  }
  .contact-panel__tab {
    position: absolute;
    left: -8px; top: 96px;
    width: 16px; height: 168px;
    background: var(--tab);
    clip-path: polygon(50% 0, 100% 6%, 100% 94%, 50% 100%, 0 94%, 0 6%);
  }
  .contact {
    position: absolute;
    left: 34px; top: 92px;
    color: var(--panel-text);
    font-size: 13px;
    line-height: 1.55;
  }
  .contact__name { font-weight: 700; font-size: 15px; letter-spacing: 0.3px; }
  .contact__role { margin-bottom: 8px; }
  .contact__row { display: flex; align-items: center; gap: 8px; }
  .contact__row svg { width: 11px; height: 11px; flex: none; }
  .contact__address { margin-top: 10px; }

  .card--back .wordmark { left: 132px; top: 128px; }
  .website {
    position: absolute;
    left: 0; right: 0; top: 290px;
    text-align: center;
    font-family: "Josefin Sans", Arial, sans-serif;
    font-weight: 300;
    font-size: 17px;
    letter-spacing: 6px;
    color: var(--muted);
  }
</style>
</head>
<body>
  <section class="card card--front" aria-label="Business card front">
    <div class="wordmark">
      <span class="wordmark__square"></span>
      <div class="wordmark__text">
        <span class="wordmark__name">CORVANE</span>
        <span class="wordmark__sub">HOLDINGS</span>
      </div>
    </div>
    <div class="contact-panel">
      <div class="contact-panel__tab"></div>
      <div class="contact">
        <p class="contact__name">KHALID BIN TARRAFI</p>
        <p class="contact__role">Managing Director</p>
        <p class="contact__row">
          <svg viewBox="0 0 12 12" aria-hidden="true"><path fill="currentColor" d="M2.5 0.8l2 2-1 1.3c.6 1.4 1.6 2.4 3 3l1.3-1 2 2-1.2 1.6C5.6 9.6 2.4 6.4 1 2z"/></svg>
          +971 4 387 2940
        </p>
        <p class="contact__row">
          <svg viewBox="0 0 12 12" aria-hidden="true"><rect x="3" y="0.8" width="6" height="10.4" rx="1" fill="none" stroke="currentColor" stroke-width="1.2"/><circle cx="6" cy="9.3" r="0.7" fill="currentColor"/></svg>
          +971 50 518 2403
        </p>
        <p class="contact__row">
          <svg viewBox="0 0 12 12" aria-hidden="true"><rect x="0.8" y="2.5" width="10.4" height="7" fill="currentColor"/><path d="M0.8 2.5L6 6.6 11.2 2.5" fill="none" stroke="#3e3d55" stroke-width="1"/></svg>
          khalid@corvane.ae
        </p>
        <p class="contact__address">Q-Span Plaza, officw 18-B07,<br>Warqa Gardens, Dubai</p>
      </div>
    </div>
  </section>

  <section class="card card--back" aria-label="Business card back">
    <div class="wordmark">
      <span class="wordmark__square"></span>
      <div class="wordmark__text">
        <span class="wordmark__name">CORVANE</span>
        <span class="wordmark__sub">HOLDINGS</span>
      </div>
    </div>
    <p class="website">www.corvane.ae</p>
  </section>
</body>
</html>
```